Dental Implant Logo and Business Card for Local Dentist

Design a unique business card and a logo that incorporates a dental implant as a primary focal point or a part of the text. New logo design & business card needs to incorporate our businesses old star shaped logo (attached) and a dental implant, along with our business name. Star logo does not have to remain the exact same colors and can be any size. Looking for a warm, friendly (non-aggressive) design that uses colors in the blue-green palate, partial to mint-turquoise color similar to the images attached . SIMPLE IS GOOD, but looking for creativity to bring all the elements together. OK to incorporate a splash of color. I have attached a few images of implant logos I like along with our existing star shaped logo. *I have also uploaded some images that represent local landscapes & images for the back of the business card. I would like to include a silhouette or sketch that represents one one of these areas on the back of the business card to convey the connection to our community and local roots of our business since we are 4th generation members of this community . Can visit our dental practice website for more info. www.hartwellandodegarddentalcare.example Card Must Haves on Front of Card:1. business name "Hartwell & Odegard Dental Care" 2. My Name: "Colin Odegard D.D.S."3. Phone # (925) 754-6020Other info for card (can be front or back)Address: 7840 Quarry Ridge Rd. #2C Larkmont Valley 94531e-mail: millerandsimarrodentalcare@gmail.comcosmetic, family, & impDesign a unique business card and a logo that incorporates a dental implant as a primary focal point or a part of the text. New logo design & business card needs to incorporate our businesses old star shaped logo (attached) and a dental implant, along with our business name. Star logo does not have to remain the exact same colors and can be any size. Looking for a warm, friendly (non-aggressive) design that uses colors in the blue-green palate, partial to mint-turquoise color similar to the images attached . SIMPLE IS GOOD, but looking for creativity to bring all the elements together. OK to incorporate a splash of color. I have attached a few images of implant logos I like along with our existing star shaped logo. *I have also uploaded some images that represent local landscapes & images for the back of the business card. I would like to include a silhouette or sketch that represents one one of these areas on the back of the business card to convey the connection to our community and local roots of our business since we are 4th generation members of this community . Can visit our dental practice website for more info. www.hartwellandodegarddentalcare.example Card Must Haves on Front of Card:1. business name "Hartwell & Odegard Dental Care" 2. My Name: "Colin Odegard D.D.S."3. Phone # (925) 754-6020Other info for card (can be front or back)Address: 7840 Quarry Ridge Rd. #2C Larkmont Valley 94531e-mail: millerandsimarrodentalcare@gmail.comcosmetic, family, & implant dentistry

Target Market(s)

Families

Industry/Entity Type

Dental

Contact Information for Business Card

See Project description above

Logo Text

Hartwell & Odegard Dental Care

Font styles to use
Serif

Colors
ffffff
33b8a4
87cfc6
0492cd
33a6d7
0255a3

Requirements
Must have
• *See Description...
• Card Must Haves on Front of Card:
• 1. business name "Hartwell & Odegard Dental Care"
• 2. My Name: "Colin Odegard D.D.S."
• 3. Phone # (555) 318-4297
• Other info for card (can be front or back)
• Address: 7840 Quarry Ridge Rd. #2C Larkmont Valley 90217
• e-mail: hartwellandodegarddentalcare@example-mail.com
Nice to have
• Local image sketch or silhouette on back side of business card with remaining information on back: address, website, e-mail etc.

```html
<!DOCTYPE html>
<html lang="en">
<head>
<meta charset="utf-8">
<title>Hartwell &amp; Odegard Dental Care — Business Card</title>
<link rel="stylesheet" href="https://fonts.googleapis.com/css2?family=Cinzel:wght@600&family=Nunito:wght@400;600&display=swap">
<style>
  :root {
    --stage: #3b3c3f;
    --card-blue: #1793d1;
    --brand-blue: #0492cd;
    --teal: #29b8a4;
    --white: #ffffff;
    --ink: #2c2c2c;
  }
  * { box-sizing: border-box; margin: 0; padding: 0; }
  html, body { width: 1200px; height: 899px; overflow: hidden; }
  body { background: var(--stage); position: relative; font-family: "Nunito", sans-serif; }

  .card {
    position: absolute;
    width: 600px;
    height: 343px;
    border-radius: 26px;
    overflow: hidden;
    box-shadow: 0 14px 30px rgba(0,0,0,.45);
  }

  /* Back of card */
  .card-back { left: 60px; top: 60px; background: var(--card-blue); color: var(--white); }
  .card-back .brand {
    position: absolute; left: 0; right: 0; top: 130px;
    text-align: center;
    font-family: "Cinzel", serif; font-weight: 600;
    color: var(--white);
  }
  .brand-name { display: block; font-size: 30px; letter-spacing: 1px; line-height: 1.1; }
  .brand-sub { display: block; font-size: 14px; letter-spacing: 6px; margin-top: 4px; }
  .brand-sub::before, .brand-sub::after {
    content: ""; display: inline-block; width: 70px; height: 1.5px;
    background: currentColor; vertical-align: middle; margin: 0 12px;
  }
  .card-back .tagline {
    position: absolute; left: 0; right: 0; top: 222px;
    text-align: center; font-size: 15px; letter-spacing: .4px;
  }

  /* Front of card */
  .card-front { left: 540px; top: 496px; background: var(--white); }
  .card-front .brand {
    position: absolute; right: 34px; top: 62px;
    text-align: center;
    font-family: "Cinzel", serif; font-weight: 600;
    color: var(--brand-blue);
  }
  .card-front .brand-name { font-size: 22px; }
  .card-front .brand-sub { font-size: 11px; letter-spacing: 5px; }
  .card-front .brand-sub::before, .card-front .brand-sub::after { width: 40px; margin: 0 8px; }

  .name-band {
    position: absolute; left: 0; right: 0; top: 170px; height: 30px;
    background: var(--teal);
  }
  .doctor-name {
    position: absolute; left: 34px; top: 166px;
    font-family: "Cinzel", serif; font-weight: 600;
    font-size: 25px; color: var(--white); letter-spacing: .5px;
    line-height: 38px;
  }
  .address {
    position: absolute; right: 34px; top: 218px;
    font-size: 15px; line-height: 1.35; color: var(--ink); text-align: right;
  }
  .contact {
    position: absolute; left: 34px; bottom: 30px;
    list-style: none; font-size: 15px; color: var(--ink);
  }
  .contact li { display: flex; align-items: center; gap: 10px; margin-top: 6px; }
  .contact svg { width: 16px; height: 16px; fill: var(--brand-blue); flex: none; }
</style>
</head>
<body>

<section class="card card-back" aria-label="Card back">
  <div class="brand">
    <span class="brand-name">Hartwell &amp; Odegard</span>
    <span class="brand-sub">Dental Care</span>
  </div>
  <p class="tagline">Comcosmetic, Family, &amp; Implant Dentistry</p>
</section>

<section class="card card-front" aria-label="Card front">
  <div class="brand">
    <span class="brand-name">Hartwell &amp; Odegard</span>
    <span class="brand-sub">Dental Care</span>
  </div>

  <div class="name-band"></div>
  <h1 class="doctor-name">Colin Odegard D.D.S.</h1>

  <p class="address">7840 Quarry Ridge Rd. #2C<br>Larkmont Valley 90217</p>

  <ul class="contact">
    <li>
      <svg viewBox="0 0 24 24" aria-hidden="true"><path d="M6.6 10.8a15.1 15.1 0 0 0 6.6 6.6l2.2-2.2a1 1 0 0 1 1-.25 11.4 11.4 0 0 0 3.6.57 1 1 0 0 1 1 1V20a1 1 0 0 1-1 1A17 17 0 0 1 3 4a1 1 0 0 1 1-1h3.5a1 1 0 0 1 1 1c0 1.25.2 2.45.57 3.57a1 1 0 0 1-.25 1z"/></svg>
      (555) 318-4297
    </li>
    <li>
      <svg viewBox="0 0 24 24" aria-hidden="true"><path d="M2 5h20v14H2z"/><path d="M2 5l10 8 10-8" fill="none" stroke="#fff" stroke-width="1.8"/></svg>
      hartwellandodegarddentalcare@example-mail.com
    </li>
  </ul>
</section>

</body>
</html>
```